Illustrations, Icons and placement

Wire frame will describe it best, https://plavido.com/diagrams/kRtmWbNoQeprsLvx

With the direction of my mockups I am going to require illustrations with similarity to the mock up. I need icons for my slider and of course beautiful slides. It is not necessary to design the webpage, I know where I want to go with this, I really just need strong illustrations.

This is the first serious design submitted. I appreciate the obvious hard work. To be honest, this system is not great for designers to know exactly what I want but finding a designer that can put in the effort to get there is the trick.

I have locked in the front page design to something that is very accurately portrayed in the mockup. The reason why is the illustration I will using. Currently My mock up shows flower on a hill, i replace with an brightcrate illustration, see uploaded file to review... Also, colors are definatly what I am looking for but this ok for now. Your design is good..

Reason: my choice needs more time to finish the design before we begin

Target Market(s)

SaaS Consumer

Industry/Entity Type

Work

Requirements
Must have
• Display features in a nice slider like

http://www.drovelink.com/pebblegate/index.php

room in header for new illustration, see attachment
Should not have
• Traditional out dated designs that look like templates

```html
<!DOCTYPE html>
<html lang="en">
<head>
<meta charset="utf-8">
<title>Find Professionals</title>
<link rel="stylesheet" href="https://fonts.googleapis.com/css2?family=Tinos:wght@400;700&family=PT+Sans:wght@400;700&display=swap">
<style>
:root{
  --bg:#070605;
  --nav-top:#1a1209;
  --nav-bottom:#0c0906;
  --label:#a88466;
  --teal:#4fc3cc;
  --teal-deep:#3aa6b1;
  --teal-head:#3b9ea4;
  --tab-top:#55c7cf;
  --tab-bottom:#00a8b8;
  --body-brown:#8b6a52;
  --ink:#3a342e;
  --gold:#8d6a2c;
  --panel:#000;
  --btn-top:#f1e25c;
  --btn-bottom:#f9b52e;
  --btn-mark:#c98a1e;
  --white:#f1f1f1;
}
*{box-sizing:border-box;margin:0;padding:0}
html,body{width:1200px;height:901px;overflow:hidden}
body{
  position:relative;
  background:
    radial-gradient(ellipse 700px 120px at 600px 901px, rgba(90,55,20,.35), transparent 70%),
    var(--bg);
  font-family:"PT Sans",sans-serif;
}
.main-nav{
  position:absolute;left:108px;top:0;width:957px;height:136px;
  background:linear-gradient(var(--nav-top),var(--nav-bottom));
  box-shadow:0 0 30px rgba(0,0,0,.8);
}
.nav-item{
  position:absolute;top:0;width:140px;margin-left:-70px;text-align:center;
  font-family:"Tinos",serif;font-weight:700;font-size:15px;line-height:18px;color:var(--label);
}
.nav-item svg{display:block;margin:0 auto;height:72px}
.nav-item .label{position:absolute;left:0;right:0}
.nav-item.active{color:var(--teal)}

.count-card{
  position:absolute;left:172px;top:214px;width:316px;height:305px;
  border-radius:7px;
  background:linear-gradient(var(--teal),var(--teal-deep));
  box-shadow:0 1px 3px rgba(0,0,0,.6),inset 0 1px 0 rgba(255,255,255,.3);
  text-align:center;color:var(--ink);font-family:"Tinos",serif;
  text-shadow:0 1px 0 rgba(255,255,255,.3);
}
.count-card .count{position:absolute;top:26px;left:0;right:0;font-size:48px}
.count-card .caption{position:absolute;top:95px;left:0;right:0;font-size:20px}
.count-card .rule{position:absolute;top:145px;left:58px;width:195px;height:3px;background:#111;box-shadow:0 1px 0 rgba(255,255,255,.4)}
.count-card .tagline{position:absolute;top:184px;left:20px;right:20px;font-size:24px;font-weight:700;line-height:41px}

.divider{position:absolute;left:541px;top:185px;width:3px;height:360px;
  background:linear-gradient(transparent,#8a6a4e 50%,transparent)}

.feature{position:absolute}
.feature h3{font-family:"Tinos",serif;font-weight:700;font-size:19.5px;color:var(--teal-head);margin-bottom:10px;white-space:nowrap}
.feature p{font-size:15px;line-height:23px;color:var(--body-brown)}

.dev-panel{
  position:absolute;left:108px;top:568px;width:957px;height:360px;
  background:var(--panel);border-radius:16px;
}
.tab{
  position:absolute;top:18px;width:60px;height:330px;border-radius:3px;
  background:linear-gradient(var(--tab-top),var(--tab-bottom));
  display:flex;align-items:center;justify-content:flex-start;flex-direction:column;
}
.tab span{
  writing-mode:vertical-rl;transform:rotate(180deg);
  font-weight:700;font-size:23.5px;color:var(--white);
  text-shadow:0 1px 2px rgba(0,0,0,.4);white-space:nowrap;
}
.dev-title{position:absolute;left:186px;top:26px;font-family:"Tinos",serif;font-weight:400;font-size:25px;color:var(--gold)}
.dev-copy{position:absolute;left:192px;top:80px;width:240px;font-size:13.4px;line-height:23px;color:var(--white)}
.dev-copy p+p{margin-top:14px}
.platform{
  position:absolute;left:450px;width:252px;height:80px;border-radius:6px;
  background:linear-gradient(var(--btn-top),var(--btn-bottom));
  box-shadow:0 1px 2px rgba(255,255,255,.2);
  display:flex;align-items:center;
  font-family:"Tinos",serif;font-size:23px;line-height:28px;color:var(--ink);
}
.platform .mark{width:56px;height:56px;border-radius:50%;background:var(--btn-mark);margin:0 18px 0 26px;flex:none}
.platform .name{flex:1;text-align:center;padding-right:12px}
</style>
</head>
<body>

<nav class="main-nav">
  <div class="nav-item" style="left:126px">
    <svg viewBox="0 0 120 72" width="120"><g fill="#000"><circle cx="32" cy="18" r="14"/><path d="M6 66c0-22 10-32 26-32s26 10 26 32z"/><circle cx="85" cy="18" r="14"/><path d="M59 66c0-22 10-32 26-32s26 10 26 32z"/></g></svg>
    <div class="label" style="top:88px">Collaborate</div>
  </div>
  <div class="nav-item active" style="left:270px">
    <svg viewBox="0 0 80 72" width="80"><g fill="#49bcc4"><circle cx="28" cy="16" r="14"/><path d="M2 66c0-22 10-32 26-32s26 10 26 32z"/></g><path d="M25 34h6l-1 22-2 4-2-4z" fill="#111"/><circle cx="60" cy="26" r="9" fill="none" stroke="#49bcc4" stroke-width="3"/><path d="M66 33l10 9" stroke="#49bcc4" stroke-width="4"/></svg>
    <div class="label" style="top:80px">Find<br>Professionals</div>
  </div>
  <div class="nav-item" style="left:406px">
    <svg viewBox="0 0 70 72" width="70"><ellipse cx="32" cy="12" rx="24" ry="7" fill="#111"/><path d="M8 12v44c0 5 11 8 24 8s24-3 24-8V12c0 5-11 8-24 8S8 17 8 12z" fill="#000"/><path d="M50 50c6 6 14 10 10 14" stroke="#000" stroke-width="4" fill="none"/></svg>
    <div class="label" style="top:80px">Theme<br>Builder</div>
  </div>
  <div class="nav-item" style="left:548px">
    <svg viewBox="0 0 84 72" width="84"><g fill="#000"><ellipse cx="42" cy="10" rx="38" ry="9"/><path d="M4 16c0 5 17 9 38 9s38-4 38-9v14c0 5-17 9-38 9S4 35 4 30z"/><path d="M4 36c0 5 17 9 38 9s38-4 38-9v14c0 5-17 9-38 9S4 55 4 50z"/></g></svg>
    <div class="label" style="top:89px">Hosting</div>
  </div>
  <div class="nav-item" style="left:689px">
    <svg viewBox="0 0 74 72" width="74"><g stroke="#000" stroke-width="10" stroke-linecap="round"><path d="M12 62L56 18"/><path d="M14 14l46 46"/></g><circle cx="58" cy="14" r="10" fill="#000"/></svg>
    <div class="label" style="top:80px">Developer<br>Tools</div>
  </div>
  <div class="nav-item" style="left:828px">
    <svg viewBox="0 0 72 72" width="72"><g stroke="#000" stroke-width="4"><path d="M36 8v56M8 36h56M16 16l40 40M56 16L16 56"/></g><circle cx="36" cy="36" r="8" fill="#000"/><g fill="#000"><path d="M36 0l6 9h-12zM36 72l6-9h-12zM0 36l9-6v12zM72 36l-9-6v12z"/></g></svg>
    <div class="label" style="top:91px">Distributions</div>
  </div>
</nav>

<section class="count-card">
  <div class="count">4,258</div>
  <div class="caption">DEVELOPERS AVAILABLE</div>
  <div class="rule"></div>
  <div class="tagline">Find the one that’s right for you</div>
</section>

<div class="divider"></div>

<section class="feature" style="left:585px;top:206px;width:220px">
  <h3>SEARCH DEVELOPERS</h3>
  <p>Dictumst purus augue, a amet, lundium augue, cras, etiam dipice parturient augue, tempor cum pellentesque. Lectus</p>
</section>
<section class="feature" style="left:843px;top:206px;width:210px">
  <h3>REVIEW REPUTATION</h3>
  <p>Sed est sed pulvinar montes arcu nec magna, turpis purus ridiculus. Integer lacus egestas.</p>
</section>
<section class="feature" style="left:585px;top:382px;width:212px">
  <h3>ESCROW ACCOUNTS</h3>
  <p>Dictumst purus augue, a amet, lundium augue, cras, etiam adipiscing parturient augue, tempor cum pellentesque.</p>
</section>
<section class="feature" style="left:840px;top:382px;width:212px">
  <h3>CONTROL ACCESS</h3>
  <p>Dictumst purus augue, a amet, lundium augue, cras, etiam adipiscing parturient augue, tempor cum pellentesque.</p>
</section>

<section class="dev-panel">
  <div class="tab" style="left:34px;justify-content:center"><span style="margin-top:-20px">Portfolios</span></div>
  <div class="tab" style="left:99px;padding-top:18px"><span>The Right Dev For The Job</span></div>

  <h2 class="dev-title">The Right Dev For The Job</h2>
  <div class="dev-copy">
    <p>Montes turpis cum dignissim vel lorem tortor proin mid augue. Nec eros mus adipiscing. Ac, odio tincidunt augue, magnis scelerisque urna.</p>
    <p>Proin auctor integer scelerisque turpis, turpis facilisis? Dolor in. In, placerat. Placerat integer pellentesque. Phasellus mauris. Sed eros. Scelerisque dolor hac parturient.</p>
  </div>

  <div class="platform" style="top:64px"><span class="mark"></span><span class="name">Larkspire<br>Developers</span></div>
  <div class="platform" style="top:150px"><span class="mark"></span><span class="name">Tidemill<br>Developers</span></div>
  <div class="platform" style="top:235px"><span class="mark"></span><span class="name">Corvane<br>Developers</span></div>

  <div class="tab" style="left:738px;padding-top:34px"><span>Know Their Experience</span></div>
  <div class="tab" style="left:803px;padding-top:50px"><span>Read/Write Reviews</span></div>
  <div class="tab" style="left:867px;padding-top:46px"><span>Rate Your Developer</span></div>
</section>

</body>
</html>
```